LLC needs a business card design that emphasizes consulting and expert witness in upstream oil and g

I need a business card design for my company called Obena Consultative Service, LLC. My expertise is in oil and gas upstream operations management to optimize performance and also as an expert witness for law firms in oil and gas upstream operations litigation.
The final design should communicate knowledge and hands-on experience as well as trust. (Obena means rope or lasso. Perhaps "Obena" should be in the form of a rope.) I do not like the color green in any shade. My first preference would be some shade of blue.
Industry/Entity Type
Oil And Gas

```html
<!DOCTYPE html>
<html lang="en">
<head>
<meta charset="utf-8">
<title>Obena Consultative Service, LLC — Business Card</title>
<link href="https://fonts.googleapis.com/css2?family=Arimo:wght@400;700&display=swap" rel="stylesheet">
<style>
  :root{
    --bg:#e9e6e1;
    --paper:#fbfbfb;
    --blue:#2a4f98;
    --blue-light:#3a63ad;
    --ink:#2f4f96;
    --muted:#5d6f9a;
    --red:#c0392b;
    --yellow:#f2d21b;
    --rule:#9aa6c2;
  }
  *{box-sizing:border-box;margin:0;padding:0}
  html,body{width:1200px;height:902px;overflow:hidden;background:var(--bg)}
  body{font-family:"Arimo",Arial,sans-serif;color:var(--ink);position:relative}
  .card{position:absolute;left:300px;width:600px;height:343px;background:var(--paper);
        box-shadow:0 6px 18px rgba(0,0,0,.18);overflow:hidden}
  .card--front{top:70px}
  .card--back{top:480px}
  .card__bands{position:absolute;inset:0;width:100%;height:100%}
  .brand{position:absolute;color:var(--ink);font-weight:400;white-space:nowrap}
  .card--front .brand{left:0;right:0;top:150px;text-align:center;font-size:31px}
  .card--back .brand{left:40px;top:64px;font-size:19px}
  .brand-rule{position:absolute;left:40px;top:96px;width:250px;height:1px;background:var(--rule)}
  .employee{position:absolute;left:76px;top:196px}
  .employee__name{font-size:25px;color:var(--ink)}
  .employee__title{font-size:11px;color:var(--muted);margin-top:4px;margin-left:18px}
  .address{position:absolute;right:40px;top:52px;width:250px;text-align:right;font-size:12px;
           line-height:1.35;color:var(--ink)}
  .contact-rule{position:absolute;right:40px;width:230px;height:1px;background:var(--rule)}
  .contact-rule--top{top:94px}
  .contact-rule--bottom{top:224px}
  .contacts{position:absolute;left:340px;top:106px;list-style:none}
  .contacts li{display:flex;align-items:center;gap:8px;font-size:12.5px;height:28px;color:var(--ink)}
  .contacts svg{width:16px;height:16px;flex:none}
</style>
</head>
<body>

<section class="card card--front" aria-label="Card front">
  <svg class="card__bands" viewBox="0 0 600 343" aria-hidden="true">
    <rect x="0" y="0" width="600" height="36" fill="var(--blue)"/>
    <polygon points="0,0 232,0 220,36 0,36" fill="var(--blue-light)"/>
    <polygon points="232,0 244,0 232,36 220,36" fill="var(--yellow)"/>
    <polygon points="244,0 252,0 240,36 232,36" fill="var(--red)"/>
    <rect x="0" y="278" width="600" height="65" fill="var(--blue)"/>
    <polygon points="0,278 420,278 400,343 0,343" fill="var(--blue-light)"/>
    <polygon points="420,278 432,278 412,343 400,343" fill="var(--yellow)"/>
    <polygon points="432,278 440,278 420,343 412,343" fill="var(--red)"/>
  </svg>
  <div class="brand">Obena Consultative Service, LLC</div>
</section>

<section class="card card--back" aria-label="Card back">
  <svg class="card__bands" viewBox="0 0 600 343" aria-hidden="true">
    <rect x="0" y="0" width="600" height="36" fill="var(--blue)"/>
    <polygon points="0,0 250,0 238,36 0,36" fill="var(--blue-light)"/>
    <polygon points="250,0 262,0 250,36 238,36" fill="var(--yellow)"/>
    <polygon points="262,0 270,0 258,36 250,36" fill="var(--red)"/>
    <rect x="0" y="278" width="600" height="65" fill="var(--blue)"/>
    <polygon points="0,278 460,278 440,343 0,343" fill="var(--blue-light)"/>
    <polygon points="460,278 472,278 452,343 440,343" fill="var(--yellow)"/>
    <polygon points="472,278 480,278 460,343 452,343" fill="var(--red)"/>
  </svg>

  <div class="brand">Obena Consultative Service, LLC</div>
  <div class="brand-rule"></div>

  <div class="employee">
    <div class="employee__name">Employee name</div>
    <div class="employee__title">Managing Director</div>
  </div>

  <div class="address">Your Address Inc 2nd Lane Ave Brookfield,<br>NJ 00000</div>
  <div class="contact-rule contact-rule--top"></div>

  <ul class="contacts">
    <li>
      <svg viewBox="0 0 16 16" aria-hidden="true"><circle cx="8" cy="8" r="7" fill="none" stroke="var(--ink)"/><path d="M5.5 4.5l1.5 0 .6 1.8-.9.7a5 5 0 0 0 2.3 2.3l.7-.9 1.8.6v1.5c-3.6.4-6.4-2.4-6-6z" fill="var(--ink)"/></svg>
      555-4582 0415
    </li>
    <li>
      <svg viewBox="0 0 16 16" aria-hidden="true"><circle cx="8" cy="8" r="7" fill="none" stroke="var(--ink)"/><rect x="5.8" y="4" width="4.4" height="8" rx="0.8" fill="none" stroke="var(--ink)"/></svg>
      555-2589 0584
    </li>
    <li>
      <svg viewBox="0 0 16 16" aria-hidden="true"><circle cx="8" cy="8" r="7" fill="none" stroke="var(--ink)"/><rect x="4.5" y="5" width="7" height="5" fill="none" stroke="var(--ink)"/><path d="M6.5 11.5h3" stroke="var(--ink)"/></svg>
      www.obenaconsult.com
    </li>
    <li>
      <svg viewBox="0 0 16 16" aria-hidden="true"><circle cx="8" cy="8" r="7.5" fill="var(--ink)"/><rect x="4.5" y="5.5" width="7" height="5" fill="#fff"/><path d="M4.5 5.5l3.5 3 3.5-3" fill="none" stroke="var(--ink)"/></svg>
      info@obenaconsult.com
    </li>
  </ul>
  <div class="contact-rule contact-rule--bottom"></div>
</section>

</body>
</html>
```